Commercial Real Estate for Lease Listing Flyer

I am looking to put together a flyer for our available office space in our building. It needs to look professional and it will be standard sized 8.5 x 11 and double sided. Full color as well. This flyer will need to be able to be put in a PDF and a picture file that can be embedded in an email. I have included pictures, logo, and a Word document with the information you should need. Also, I included a bunch of SAMPLE leasing flyers that you can get ideas from. The floor plan is also included in here. I want it specifically noted that the top suite is Suite 100 and the bottom suite is 120. And list their size as well. I will be reviewing all designs very quickly, so be sure to check the comments.

• Please refer to these links for additional photos:
• "Twilight 1.jpg" at: https://files.plinthdocs.net/a/preview/3f7d1a92-b4e0-4c1a-8e5f-71c0d2ab9e34
• Twilight 2_straightened.jpg" at: https://files.plinthdocs.net/a/preview/a15c8e03-7d2b-4f9e-b6a1-0c93e4f72d58
• "Twilight 3.jpg" at: https://files.plinthdocs.net/a/preview/6e2b9f71-c3a4-4d08-9e7b-5f1a8c03d6e2
• "Twilight 4.jpg" at: https://files.plinthdocs.net/a/preview/c84a0d6e-1f3b-4e57-a2c9-9b7e05f4d813
• "Twilight 5.jpg" at: https://files.plinthdocs.net/a/preview/7b0f5c28-e6d1-4a93-8f4e-d25a1b6c07f9
• "Twilight 6.jpg" at: https://files.plinthdocs.net/a/preview/e3c6a417-5b92-4f0d-bc8e-4a1f97d2e065
• "Twilight 7.jpg" at: https://files.plinthdocs.net/a/preview/5a9d2e80-c7f4-4b16-93a0-e8b6f1c4d27a
• "Twilight 8.jpg" at: https://files.plinthdocs.net/a/preview/b2e7f069-84c3-4d5a-a71e-3c0d9b58f6e4
• "Twilight 9.jpg" at: https://files.plinthdocs.net/a/preview/4d8c1b3f-a0e5-4f72-8b69-f17e2c05a9d3
• "Twilight 10.jpg" at: https://files.plinthdocs.net/a/preview/f09a6c52-3e18-4b7d-9c24-6b5d80e1f3a7
• "Twilight 11.jpg" at: https://files.plinthdocs.net/a/preview/8e4f2d06-b9c7-4a31-85e0-d7a3c16f4b92

```html
<!DOCTYPE html>
<html lang="en">
<head>
<meta charset="utf-8">
<title>Harbor Road Centre – Leasing Flyer</title>
<link href="https://fonts.googleapis.com/css2?family=Montserrat:wght@400;600;700&family=Raleway:wght@400;500&family=Open+Sans:wght@400;600;700&display=swap" rel="stylesheet">
<style>
:root{
  --bg:#e4e5e8;
  --charcoal:#3a3839;
  --gold:#cfae6c;
  --gold-light:#e2cd92;
  --beige:#e6d7a3;
  --brown:#5e4a36;
  --navy:#1f3f7a;
  --orange:#e8762b;
  --blue:#1a8fd0;
  --ink:#3a3a3a;
  --white:#ffffff;
}
*{box-sizing:border-box;margin:0;padding:0}
html,body{width:1200px;height:1200px;overflow:hidden;background:var(--bg)}
body{position:relative;font-family:"Open Sans",Arial,sans-serif}

/* front page */
.front{position:absolute;left:27px;top:44px;width:575px;height:742px;background:var(--white)}
.photo{position:absolute}
.photo.top-left{left:0;top:0;width:287px;height:158px;background:linear-gradient(180deg,#d6b27a 0%,#c79f63 55%,#56634a 80%,#4c4c4c 100%)}
.photo.top-right{left:289px;top:0;width:286px;height:158px;background:linear-gradient(180deg,#8ea4d6 0%,#c3a6b8 35%,#caa46a 60%,#3f5d37 85%,#5a5a5a 100%)}
.title-band{position:absolute;left:0;top:158px;width:575px;height:156px;background:var(--charcoal)}
.title-inner{position:absolute;left:73px;top:10px;width:440px;text-align:center}
.title-band h1{font-family:"Montserrat",sans-serif;font-weight:600;font-size:40px;color:var(--gold);line-height:60px;white-space:nowrap}
.title-band .address{border-top:1px solid var(--gold);border-bottom:1px solid var(--gold);margin-top:5px;padding:6px 0 7px;font-family:"Raleway",sans-serif;font-size:17.5px;color:var(--white);white-space:nowrap}
.title-band .offer{margin-top:14px;font-family:"Montserrat",sans-serif;font-weight:700;font-size:15.5px;color:var(--white);letter-spacing:.5px;white-space:nowrap}
.photo.hero{left:0;top:314px;width:575px;height:289px;background:linear-gradient(180deg,#9aa6cf 0%,#c8a77e 30%,#d1a867 50%,#3e6035 75%,#4d4d4d 100%)}
.thumbs{position:absolute;left:0;top:606px;width:575px;height:104px;display:flex;gap:3px}
.thumbs .photo{position:static;flex:1;background:linear-gradient(180deg,#d8cba2 0%,#b9a170 60%,#6e5a3e 100%)}
.front-footer{position:absolute;left:0;top:710px;width:575px;height:32px;display:flex;align-items:center;justify-content:center;font-size:10.5px;color:#555;gap:4px;white-space:nowrap}
.front-footer b{color:#222}
.front-footer .phone{color:var(--orange);font-weight:700}
.front-footer .email{color:var(--blue);font-weight:600}
.front-footer .sep{color:#aaa;margin:0 4px}

/* back page */
.back{position:absolute;left:624px;top:454px;width:548px;height:708px;background:var(--beige)}
.back .side{position:absolute;left:308px;top:0;width:240px;height:626px;background:var(--brown)}
.corner{position:absolute;left:372px;top:0;width:176px;height:160px;background:linear-gradient(135deg,#e6cf95,#c9a862)}
.rate{position:absolute;right:10px;top:18px;text-align:right;font-family:"Montserrat",sans-serif;font-weight:700;color:var(--brown)}
.rate .label{display:inline-block;font-size:10px;line-height:10px;vertical-align:middle}
.rate .amount{font-size:24px;vertical-align:middle}
.rate .amount small{font-size:12px}
.rate .unit{display:inline-block;font-size:9px;line-height:10px;text-align:left;vertical-align:middle}
.rate .note{display:block;margin-top:8px;font-size:10.5px;line-height:10.5px}
.plan{position:absolute;left:8px;top:30px;width:324px;height:261px;background:var(--white);border-radius:14px;padding:14px}
.plan .drawing{width:100%;height:100%;background:linear-gradient(135deg,#f4f4f4,#e2e2e2)}
.suites{position:absolute;left:346px;top:164px;width:196px;color:var(--white);font-size:9.5px;line-height:11.5px}
.suite{margin-bottom:12px}
.suite h3{display:inline;font-family:"Montserrat",sans-serif;font-weight:700;font-size:14px;color:var(--gold)}
.combined{font-family:"Montserrat",sans-serif;font-size:12px;line-height:16px;color:var(--gold);margin-top:-2px}
.features{position:absolute;left:346px;top:362px;width:182px}
.features h2{font-family:"Montserrat",sans-serif;font-weight:700;font-size:20px;line-height:19px;color:var(--gold);margin-bottom:22px}
.features li{list-style:none;font-weight:700;font-size:9.5px;line-height:11px;color:var(--white);padding-bottom:5px;margin-bottom:9px;border-bottom:1px solid var(--gold)}
.features li:last-child{border-bottom:none}
.about{position:absolute;left:32px;top:334px;width:256px;font-family:"Raleway",sans-serif;font-size:11.5px;line-height:16px;color:var(--ink)}
.about p{padding-bottom:8px;margin-bottom:9px;border-bottom:1px solid #b89c66}
.about p:last-child{border-bottom:none}
.back-footer{position:absolute;left:0;top:626px;width:548px;height:82px;background:var(--white);display:flex;align-items:center;padding:0 26px 0 34px}
.brand{font-family:"Montserrat",sans-serif;font-weight:600;font-size:15px;color:var(--navy);width:135px;line-height:17px}
.leasing{font-family:"Montserrat",sans-serif;font-weight:700;font-size:10px;line-height:12px;color:#c6a04a;margin-left:12px;width:170px}
.leasing b{color:var(--navy)}
.contact{margin-left:auto;text-align:center}
.contact .phone{font-family:"Montserrat",sans-serif;font-weight:700;font-size:23px;color:#b98d3a;line-height:26px}
.contact .email{background:var(--navy);color:var(--white);font-size:10.5px;font-weight:600;padding:1px 10px}
</style>
</head>
<body>

<section class="front">
  <div class="photo top-left" role="img" aria-label="Photo of the building entrance with arched portico"></div>
  <div class="photo top-right" role="img" aria-label="Twilight photo of the building and parking lot with palms"></div>
  <header class="title-band">
    <div class="title-inner">
      <h1>Harbor Road Centre</h1>
      <p class="address">4180 Harbor Road, Palm Grove Springs, FL 33400</p>
      <p class="offer">CLASS A OFFICE SPACE AVAILABLE FOR LEASE</p>
    </div>
  </header>
  <div class="photo hero" role="img" aria-label="Twilight photo of the building corner framed by palm trees"></div>
  <div class="thumbs">
    <div class="photo" role="img" aria-label="Interior office with desk and arched window"></div>
    <div class="photo" role="img" aria-label="Conference room with table and chairs"></div>
    <div class="photo" role="img" aria-label="Empty office with wood door"></div>
    <div class="photo" role="img" aria-label="Office with desk and window"></div>
  </div>
  <footer class="front-footer">
    For more information, please contact : <b>Daniel Morrow</b> @ <span class="phone">555-014-2290</span><span class="sep">|</span><span class="email">daniel@morrowholdings.com</span>
  </footer>
</section>

<section class="back">
  <div class="side"></div>
  <div class="corner" role="img" aria-label="Gold page-curl corner ornament"></div>
  <div class="rate">
    <span class="label">RENTAL<br>RATE</span>
    <span class="amount"><small>$</small>32</span>
    <span class="unit">/SF<br>All in</span>
    <span class="note">NO EXTRA<br>OPERATING<br>EXPENSES</span>
  </div>

  <div class="plan"><div class="drawing" role="img" aria-label="Floor plan of Suite 100 and Suite 120"></div></div>

  <div class="suites">
    <div class="suite"><h3>Suite 100</h3> 2,303 SF Available in February 2019 or earlier. 6 offices, break room, reception area, conference room, and a large meeting room.</div>
    <div class="suite"><h3>Suite 120</h3> 1,488 SF Available Now. 2-3 offices, 1 large executive office, conference room, break room and reception area.</div>
    <p class="combined">Both suites can be combined for 3,791 SF in total.</p>
  </div>

  <div class="about">
    <p>The Harbor Road Centre is a beautiful Class A building situated in the heart of Palm Grove Springs but without the Parkway traffic.</p>
    <p>Harbor Road Centre is located directly on I-95 just off of Harbor Road.</p>
    <p>The new Linden development south entrance is being built across the street.</p>
    <p>The suites are incredibly well appointed and move-in ready with custom oak doors and millwork, 10' ceilings, floor to ceiling windows</p>
    <p>The building is very convenient to restaurants, shopping &amp; every other trade needed.</p>
  </div>

  <div class="features">
    <h2>FEATURES<br>&amp; AMENITIES</h2>
    <ul>
      <li>Completely Move-In Ready</li>
      <li>Floor-to-Ceiling Hurricane Impact Windows Throughout</li>
      <li>Plenty of Parking</li>
      <li>Close to Everything</li>
      <li>On-site Management and Ownership</li>
      <li>Some office furniture available if needed</li>
    </ul>
  </div>

  <footer class="back-footer">
    <div class="brand">MORROW<br>HOLDINGS</div>
    <p class="leasing">For leasing information,<br>please contact : <b>Daniel Morrow</b></p>
    <div class="contact">
      <div class="phone">555-014-2290</div>
      <div class="email">daniel@morrowholdings.com</div>
    </div>
  </footer>
</section>

</body>
</html>
```